Lantern Hollow Brewing Company New Website with Food Ordering

We need a wordpress-based website for a local brewery & pizza kitchen. The final design will have 6 primary pages: home page, order pizza, our beers, visit us, about us, merch store. The website must integrate with tillpoint for kitchens for online ordering for takeout and delivery. It will also a feature a selection of beers and help customers navigate to the brewery and find hours of operation. The existing website is lanternhollowbrew.example. This is a very old website.

Industry/Entity Type

Brewery and food service

Coding

Coded - Design and coding required

Number of Pages Required

5+ page

Font styles to use
Sans Serif

Requirements
Must have
• ability to integrate seamlessly with tillpoint for kitchens, 21+ age gate
Nice to have
• see attached pdf

```html
<!DOCTYPE html>
<html lang="en">
<head>
<meta charset="utf-8">
<title>Lantern Hollow Brewing Company</title>
<link href="https://fonts.googleapis.com/css2?family=Roboto+Slab:wght@300;400;600;700&display=swap" rel="stylesheet">
<style>
  :root {
    --brand-red: #c4112f;
    --ink: #2b2b2b;
    --body-text: #5a5a5a;
    --footer-bg: #2a2727;
    --white: #ffffff;
    --slab: "Roboto Slab", "Zilla Slab", "Rockwell", "DejaVu Serif", "Bitstream Vera Serif", serif;
  }
  * { box-sizing: border-box; margin: 0; padding: 0; }
  html, body { width: 889px; height: 1200px; overflow: hidden; }
  body {
    position: relative;
    background: var(--white);
    font-family: var(--slab);
    color: var(--ink);
  }

  .site-header { position: absolute; left: 0; top: 0; width: 889px; height: 84px; background: var(--white); z-index: 3; }
  .brand {
    position: absolute; left: 83px; top: 29px; width: 112px; height: 95px;
    background: var(--white); z-index: 4;
    display: flex; align-items: center; gap: 7px; padding: 0 8px;
  }
  .brand-mark { width: 12px; height: 12px; background: var(--brand-red); flex: none; }
  .brand-name { font-size: 12px; font-weight: 700; line-height: 1.2; color: var(--brand-red); }
  .main-nav { position: absolute; top: 34px; font-size: 13px; font-weight: 400; color: var(--ink); }
  .main-nav span { position: absolute; white-space: nowrap; }

  .hero { position: absolute; left: 0; top: 84px; width: 889px; height: 536px; overflow: hidden; }
  .hero-photo {
    position: absolute; inset: 0;
    background:
      radial-gradient(ellipse 9% 30% at 39% 74%, rgba(28,38,32,0.95), transparent 100%),
      radial-gradient(ellipse 9% 30% at 60% 74%, rgba(180,182,188,0.85), transparent 100%),
      radial-gradient(ellipse 12% 24% at 25% 62%, rgba(110,34,18,0.9), transparent 100%),
      radial-gradient(ellipse 12% 24% at 74% 62%, rgba(20,14,12,0.95), transparent 100%),
      radial-gradient(ellipse 70% 40% at 50% 45%, rgba(200,150,90,0.55), transparent 80%),
      linear-gradient(180deg, #2b1b10 0%, #4e3219 25%, #8a6a45 50%, #6b5238 75%, #2a1f17 100%);
  }
  .hero-title {
    position: absolute; left: 0; top: 34px; width: 889px; text-align: center;
    color: var(--white); font-size: 25px; font-weight: 600; line-height: 35px;
  }
  .hero-actions .pill { position: absolute; top: 124px; width: 117px; height: 38px; font-size: 12.5px; font-weight: 600; }
  .pill {
    display: flex; align-items: center; justify-content: center;
    background: var(--brand-red); color: var(--white); border-radius: 20px; white-space: nowrap;
  }
  .promo-burst { position: absolute; left: 139px; top: 181px; width: 96px; height: 96px; }
  .carousel-arrow { position: absolute; top: 255px; width: 26px; height: 26px; }

  .about-pizza { position: absolute; left: 0; top: 620px; width: 889px; height: 520px; }
  .photo-frame {
    position: absolute; left: 94px; top: 63px; width: 304px; height: 378px;
    border: 2px solid var(--brand-red); border-radius: 8px;
  }
  .pizza-photo {
    position: absolute; left: 103px; top: 73px; width: 303px; height: 379px; border-radius: 6px;
    background:
      radial-gradient(circle at 30% 25%, rgba(240,200,110,0.6), transparent 40%),
      radial-gradient(circle at 70% 65%, rgba(240,200,110,0.5), transparent 40%),
      linear-gradient(160deg, #8a3318 0%, #b3442a 35%, #a8321f 60%, #7a2a14 100%);
  }
  .section-title { position: absolute; left: 448px; top: 86px; font-size: 24px; font-weight: 300; color: var(--ink); white-space: nowrap; }
  .title-rule { position: absolute; left: 451px; top: 127px; width: 44px; height: 2px; background: var(--brand-red); }
  .body-copy {
    position: absolute; left: 451px; width: 336px;
    font-size: 10.4px; font-weight: 300; line-height: 21px; color: var(--body-text); text-align: justify;
  }
  .body-copy.first { top: 146px; }
  .body-copy.second { top: 292px; }
  .section-actions .pill { position: absolute; top: 379px; width: 124px; height: 41px; font-size: 13px; font-weight: 400; }

  .site-footer { position: absolute; left: 0; top: 1140px; width: 889px; height: 60px; background: var(--footer-bg); color: var(--white); }
  .copyright { position: absolute; top: 19px; width: 889px; text-align: center; font-size: 13px; font-weight: 400; }
  .build-tag { position: absolute; left: 815px; top: 38px; font-size: 10px; }
</style>
</head>
<body>
  <header class="site-header">
    <nav class="main-nav">
      <span style="left:418px">The Kitchen</span>
      <span style="left:521px">Our Beers</span>
      <span style="left:608px">Visit Us</span>
      <span style="left:684px">About Us</span>
      <span style="left:768px">Merch</span>
    </nav>
  </header>

  <section class="hero">
    <div class="hero-photo" role="img" aria-label="Two beer cans between two glasses of dark beer on a bar"></div>
    <h1 class="hero-title">Square pizza &amp; great beer in<br>Portland, Maine</h1>
    <div class="hero-actions">
      <span class="pill" style="left:197px">Order Pizza</span>
      <span class="pill" style="left:323px">Visit Us</span>
      <span class="pill" style="left:449px">Our Beers</span>
      <span class="pill" style="left:575px">About Us</span>
    </div>
    <svg class="promo-burst" viewBox="0 0 96 96" aria-label="Try Tangy! promotion">
      <polygon fill="#c4112f" points="48,2 55,30 78,12 64,36 94,40 66,50 84,76 57,62 50,94 42,64 18,82 32,56 4,54 32,42 14,18 40,30"/>
      <text x="48" y="52" fill="#fff" font-family="Roboto Slab, DejaVu Serif, serif" font-size="9" font-weight="700" text-anchor="middle" transform="rotate(-20 48 50)">Try Tangy!</text>
    </svg>
    <svg class="carousel-arrow" style="left:43px" viewBox="0 0 26 26" aria-label="Previous slide">
      <circle cx="13" cy="13" r="12" fill="none" stroke="#fff" stroke-width="1.2"/>
      <polyline points="15,8 10,13 15,18" fill="none" stroke="#fff" stroke-width="1.8"/>
    </svg>
    <svg class="carousel-arrow" style="left:819px" viewBox="0 0 26 26" aria-label="Next slide">
      <circle cx="13" cy="13" r="12" fill="none" stroke="#fff" stroke-width="1.2"/>
      <polyline points="11,8 16,13 11,18" fill="none" stroke="#fff" stroke-width="1.8"/>
    </svg>
  </section>

  <div class="brand">
    <span class="brand-mark"></span>
    <span class="brand-name">Lantern Hollow Brewing</span>
  </div>

  <section class="about-pizza">
    <div class="photo-frame"></div>
    <div class="pizza-photo" role="img" aria-label="Detroit-style square pepperoni pizza with green onions on a cooling rack"></div>
    <h2 class="section-title">What is Detroit-style pizza?</h2>
    <div class="title-rule"></div>
    <p class="body-copy first">Sed ut perspiciatis unde omnis iste natus error sit voluptatem accusantium doloremque laudantium, totam rem aperiam, eaque ipsa quae ab illo inventore veritatis et quasi architecto beatae vitae dicta sunt explicabo. Nemo enim ipsam voluptatem quia voluptas sit aspernatur aut odit aut fugit, sed quia consequuntur magni dolores eos qui ratione voluptatem sequi nesciunt.</p>
    <p class="body-copy second">Neque porro quisquam est, qui dolorem ipsum quia dolor sit amet, consectetur, adipisci velit, sed quia non numquam eius modi tempora dolore magnam aliquam quaerat voluptatem.</p>
    <div class="section-actions">
      <span class="pill" style="left:450px">Order Online</span>
      <span class="pill" style="left:584px">View Full Menu</span>
    </div>
  </section>

  <footer class="site-footer">
    <p class="copyright">© Copyright 2022 Lantern Hollow Brew.All Rights Reserved</p>
    <span class="build-tag">C2</span>
  </footer>
</body>
</html>
```